Business card for medical clinic

I need an upmarket, modern medical/health business card for my clinic

Contact Information for Business Card

name, address, email, qr code

```html
<!DOCTYPE html>
<html lang="en">
<head>
<meta charset="UTF-8">
<title>Corvale Health Group – Business Card</title>
<link rel="stylesheet" href="https://fonts.googleapis.com/css2?family=Montserrat:wght@400;500;800&display=swap">
<style>
  :root {
    --bg: #2b2d31;
    --brand-blue: #22a6e2;
    --brand-deep: #17628f;
    --brand-navy: #1b4a72;
    --ink: #1f2328;
    --paper: #ffffff;
  }
  * { margin: 0; padding: 0; box-sizing: border-box; }
  html, body { width: 1200px; height: 880px; overflow: hidden; }
  body {
    background: var(--bg);
    font-family: "Montserrat", Arial, sans-serif;
    display: flex;
    flex-direction: column;
    align-items: center;
    justify-content: center;
    gap: 44px;
  }
  .card {
    width: 630px;
    height: 360px;
    border-radius: 22px;
    position: relative;
    overflow: hidden;
  }

  /* Front */
  .card-front {
    background: linear-gradient(135deg, var(--brand-blue) 0%, #2a9fd6 35%, var(--brand-deep) 75%, #2a5f86 100%);
    display: flex;
    align-items: center;
    justify-content: center;
  }
  .front-brand {
    display: flex;
    align-items: center;
    gap: 22px;
    color: var(--paper);
  }
  .brand-dot {
    width: 64px; height: 64px;
    border-radius: 50%;
    border: 5px solid var(--paper);
    flex: none;
  }
  .front-brand .brand-name {
    font-weight: 500;
    font-size: 34px;
    letter-spacing: 3px;
    line-height: 1.2;
    text-transform: uppercase;
  }

  /* Back */
  .card-back { background: var(--paper); }
  .back-brand {
    position: absolute;
    left: 48px; top: 150px;
    display: flex; align-items: center; gap: 14px;
    color: var(--brand-navy);
  }
  .back-brand .brand-dot { width: 44px; height: 44px; border-width: 4px; border-color: var(--brand-navy); }
  .back-brand .brand-name {
    font-weight: 500; font-size: 20px; letter-spacing: 2px;
    line-height: 1.25; text-transform: uppercase;
  }
  .divider {
    position: absolute; left: 318px; top: 100px;
    width: 2px; height: 170px; background: var(--brand-blue);
  }
  .contact {
    position: absolute; left: 340px; top: 62px;
    color: var(--ink);
  }
  .contact-name {
    font-weight: 800; font-size: 28px; color: var(--brand-blue);
    text-transform: uppercase; letter-spacing: 0.5px;
  }
  .contact-role { font-size: 15px; margin-top: 2px; }
  .contact-list { list-style: none; margin-top: 16px; font-size: 15px; }
  .contact-list li { display: flex; align-items: center; gap: 8px; line-height: 22px; }
  .contact-list svg { width: 14px; height: 14px; fill: var(--brand-blue); flex: none; }
  .contact-address { margin-top: 12px; font-size: 15px; line-height: 21px; }
  .footer-band { position: absolute; left: 0; bottom: 0; }
  .website {
    position: absolute; left: 380px; bottom: 22px; width: 150px;
    text-align: center; color: var(--paper); font-size: 14px; font-weight: 500;
  }
</style>
</head>
<body>
  <section class="card card-front">
    <div class="front-brand">
      <span class="brand-dot"></span>
      <span class="brand-name">Corvale Health<br>Group</span>
    </div>
  </section>

  <section class="card card-back">
    <div class="back-brand">
      <span class="brand-dot"></span>
      <span class="brand-name">Corvale Health<br>Group</span>
    </div>

    <div class="divider"></div>

    <div class="contact">
      <h1 class="contact-name">Daniel Hart</h1>
      <p class="contact-role">Managing Director</p>
      <ul class="contact-list">
        <li><svg viewBox="0 0 24 24"><path d="M6.6 10.8a15 15 0 0 0 6.6 6.6l2.2-2.2a1 1 0 0 1 1-.25 11.4 11.4 0 0 0 3.6.57 1 1 0 0 1 1 1V20a1 1 0 0 1-1 1A17 17 0 0 1 3 4a1 1 0 0 1 1-1h3.5a1 1 0 0 1 1 1c0 1.25.2 2.45.57 3.57a1 1 0 0 1-.25 1z"/></svg>123 456 789</li>
        <li><svg viewBox="0 0 24 24"><path d="M7 1h10a2 2 0 0 1 2 2v18a2 2 0 0 1-2 2H7a2 2 0 0 1-2-2V3a2 2 0 0 1 2-2zm0 3v14h10V4zm5 15.5a1 1 0 1 0 0 2 1 1 0 0 0 0-2z"/></svg>123 456 0000</li>
        <li><svg viewBox="0 0 24 24"><path d="M2 5h20v14H2zm2 2v.5l8 5 8-5V7zm0 3v7h16v-7l-8 5z"/></svg>info@yourmail.com</li>
      </ul>
      <p class="contact-address">Your address, City<br>State, Zip 1234</p>
    </div>

    <svg class="footer-band" width="630" height="80" viewBox="0 0 630 80">
      <path d="M0 58 L352 58 L372 8 L528 8 L544 16 L630 16 L630 80 L0 80 Z" fill="var(--brand-blue)"/>
    </svg>
    <p class="website">www.yourwebsite.com</p>
  </section>
</body>
</html>
```